Civora88 - a Political Plebescite app.

There is a current app in the App Store (worldwide) and Play Store (worldwide) called yourStance (with an owl logo). The UX needs to be redesigned to make it more visually pleasing.

The requirement is to build a UX that is suitable for both iOS and Android - i.e. consistent look for both platforms. The design is to span the variety of sizes available from smart devices - phones and tablets. The layout as it stands is portrait only, and a secondary design to encompass landscape is wanted.

You would need to download the app to get a feel for all the functionality - there are 3 visible forms (currently) and a hidden form, that will be used in the near future - this hidden form will look similar to the main (first) form.

To get full functionality you need to do the following:
Go to the Options page
Toggle the top slide
Click on UNREGISTERED
Select a state/territory

I know this is a bit non-intuitive - in the "real" product these steps are automated - but for this release the user gets to choose.

Once this is done - the other button(s) appear in the top left of the screen - and data is available to be displayed.

The current forms are included in this brief. The Options screen will ultimately not be showing all the current data, only the lower slider (or other indicator) and the associated version and copyright notices. The hidden screen is much like the main screen - showing the name of the bill and information pertaining to that bill - there needs to be a button (or action site) to toggle between the main and this hidden screen.

Target Market(s)

All eligable voters (currently in Australia)

Industry/Entity Type

Political

Requirements
Should not have
• Do not present to me my own/existing design with the only change being colours and label layout.

```html
<!DOCTYPE html>
<html lang="en">
<head>
<meta charset="utf-8">
<title>Civora88 – Bill</title>
<link href="https://fonts.googleapis.com/css2?family=Roboto:wght@300;400&display=swap" rel="stylesheet">
<style>
  :root {
    --navy: #1f2f4a;
    --white: #ffffff;
    --bar-grey: #f2f2f2;
    --title-grey: #5a5a5a;
    --body-grey: #7a7a7a;
    --label-grey: #8a8a8a;
    --accent-blue: #1a86d8;
    --map-green: #4e8f6a;
    --map-red: #a9281e;
    --no-red: #e8141b;
    --yes-green: #1e8a12;
    --status-green: #14a31e;
  }
  * { box-sizing: border-box; margin: 0; padding: 0; }
  html, body { width: 674px; height: 1200px; overflow: hidden; background: var(--white); }
  body { font-family: 'Roboto', sans-serif; position: relative; }

  .top-bar { position: absolute; top: 0; left: 0; width: 674px; height: 131px; background: var(--navy); color: var(--white); }
  .status { position: absolute; top: 0; left: 0; right: 0; height: 44px; font-size: 22px; font-weight: 300; }
  .status .carrier { position: absolute; left: 14px; top: 8px; display: flex; align-items: center; gap: 6px; }
  .signal { display: flex; gap: 2px; }
  .signal span { width: 11px; height: 11px; border-radius: 50%; border: 1.5px solid var(--white); }
  .signal span.on { background: var(--white); }
  .status .time { position: absolute; left: 0; right: 0; top: 6px; text-align: center; font-size: 26px; }
  .status .battery { position: absolute; right: 12px; top: 8px; display: flex; align-items: center; gap: 8px; }
  .battery-cell { width: 50px; height: 20px; border: 2px solid var(--white); border-radius: 4px; padding: 2px; }
  .battery-cell i { display: block; width: 100%; height: 100%; background: var(--white); border-radius: 1px; }

  .region-tabs { position: absolute; left: 18px; top: 72px; display: flex; gap: 12px; }
  .region-tab { width: 40px; height: 34px; border-radius: 5px; }
  .region-tab.green { background: var(--map-green); }
  .region-tab.red { background: var(--map-red); }
  .tab-marker { position: absolute; left: 66px; top: 127px; width: 49px; height: 4px; background: var(--accent-blue); }

  .screen-title { position: absolute; left: 0; right: 0; top: 74px; text-align: center; font-size: 28px; font-weight: 400; }
  .header-actions { position: absolute; right: 18px; top: 76px; display: flex; gap: 20px; }

  .bill-bar { position: absolute; top: 131px; left: 0; width: 674px; height: 62px; background: var(--bar-grey); }
  .bill-title { position: absolute; left: 19px; top: 14px; font-size: 26px; color: var(--title-grey); font-weight: 400; }
  .no-doc { position: absolute; right: 18px; top: 11px; }

  .bill-summary { position: absolute; left: 19px; top: 210px; width: 638px; font-size: 17px; line-height: 26.2px; color: var(--body-grey); font-weight: 300; hyphens: auto; }

  .vote-options { position: absolute; top: 1005px; left: 0; right: 0; display: flex; justify-content: center; gap: 52px; }
  .vote { display: flex; flex-direction: column; align-items: center; gap: 10px; width: 70px; }
  .vote-ring { width: 70px; height: 70px; border-radius: 50%; border: 2.5px solid; display: flex; align-items: center; justify-content: center; }
  .vote-no .vote-ring { border-color: var(--no-red); }
  .vote-party .vote-ring { border-color: var(--navy); }
  .vote-yes .vote-ring { border-color: var(--yes-green); }
  .vote-label { font-size: 18px; color: var(--label-grey); }

  .footer-bar { position: absolute; bottom: 0; left: 0; width: 674px; height: 40px; background: var(--navy); color: var(--white); font-size: 18px; font-weight: 300; }
  .live-dot { position: absolute; left: 19px; top: 12px; width: 16px; height: 16px; border-radius: 50%; background: var(--status-green); }
  .chamber { position: absolute; left: 0; right: 0; top: 9px; text-align: center; }
  .position { position: absolute; right: 18px; top: 9px; }
</style>
</head>
<body>
  <header class="top-bar">
    <div class="status">
      <div class="carrier">
        <div class="signal"><span class="on"></span><span class="on"></span><span class="on"></span><span></span><span></span></div>
        NOVA
        <svg width="22" height="16" viewBox="0 0 22 16"><path d="M11 15l3-3.5a4.5 4.5 0 0 0-6 0z M4.5 8a9.5 9.5 0 0 1 13 0l-1.8 2a6.8 6.8 0 0 0-9.4 0z M1 4.2a14.5 14.5 0 0 1 20 0l-1.8 2a11.8 11.8 0 0 0-16.4 0z" fill="#fff"/></svg>
      </div>
      <div class="time">4:21 PM</div>
      <div class="battery">
        <svg width="14" height="24" viewBox="0 0 14 24"><path d="M2 6l10 11-5 5V2l5 5L2 18" fill="none" stroke="#8a93a3" stroke-width="1.6"/></svg>
        100%
        <div class="battery-cell"><i></i></div>
      </div>
    </div>
    <nav class="region-tabs">
      <div class="region-tab green" role="img" aria-label="State map icon"></div>
      <div class="region-tab red" role="img" aria-label="State map icon"></div>
      <div class="region-tab green" role="img" aria-label="National map icon"></div>
      <div class="region-tab red" role="img" aria-label="National map icon"></div>
    </nav>
    <div class="tab-marker"></div>
    <h1 class="screen-title">Title</h1>
    <div class="header-actions">
      <svg width="33" height="33" viewBox="0 0 33 33" aria-label="Help"><circle cx="16.5" cy="16.5" r="16.5" fill="var(--accent-blue)"/><text x="16.5" y="24" text-anchor="middle" font-family="Roboto, sans-serif" font-size="22" font-weight="700" fill="var(--navy)">?</text></svg>
      <svg width="34" height="34" viewBox="0 0 34 34" aria-label="Settings"><g fill="var(--accent-blue)" transform="translate(17 17)"><circle r="12"/><g><rect x="-4" y="-17" width="8" height="8" rx="1"/><rect x="-4" y="-17" width="8" height="8" rx="1" transform="rotate(45)"/><rect x="-4" y="-17" width="8" height="8" rx="1" transform="rotate(90)"/><rect x="-4" y="-17" width="8" height="8" rx="1" transform="rotate(135)"/><rect x="-4" y="-17" width="8" height="8" rx="1" transform="rotate(180)"/><rect x="-4" y="-17" width="8" height="8" rx="1" transform="rotate(225)"/><rect x="-4" y="-17" width="8" height="8" rx="1" transform="rotate(270)"/><rect x="-4" y="-17" width="8" height="8" rx="1" transform="rotate(315)"/></g><circle r="5" fill="var(--navy)"/></g></svg>
    </div>
  </header>

  <section class="bill-bar">
    <h2 class="bill-title">Crimes Amendment (Ava’s Law) Bill 2015</h2>
    <svg class="no-doc" width="41" height="41" viewBox="0 0 41 41" aria-label="Bill text unavailable"><g fill="none" stroke="#8c8c8c" stroke-width="2.2"><circle cx="20.5" cy="20.5" r="19"/><path d="M13 10h11l5 5v16H13z"/><path d="M17 18h8M17 22h8M17 26h8" stroke-width="1.6"/><path d="M7 34L34 7"/></g></svg>
  </section>

  <p class="bill-summary">Lorem ipsum dolor sit amet, consectetur adipiscing elit. Nam condimentum leo sed nisi malesuada, sed accumsan metus ultricies. Donec eleifend nibh in ultrices tempus. Morbi id tempor lorem. Suspendisse potenti. Fusce at augue pulvinar, ultricies nisl id, bibendum est. Cras semper ac nulla ut vulputate. Nam faucibus sagittis odio, quis molestie elit sollicitudin et. Nam dapibus fringilla orci, quis efficitur leo consectetur eu. Vivamus dui lectus, mollis a condimentum consequat, ullamcorper porta lectus. Vivamus sit amet justo enim. Donec nec lorem mi. Lorem ipsum dolor sit amet, consectetur adipiscing elit. Nam condimentum leo sed nisi malesuada, sed accumsan metus ultricies. Donec eleifend nibh in ultrices tempus. Morbi id tempor lorem. Suspendisse potenti. Fusce at augue pulvinar, ultricies nisl id, bibendum est. Cras semper ac nulla ut vulputate. Nam faucibus sagittis odio, quis molestie elit sollicitudin et. Nam dapibus fringilla orci, quis efficitur leo consectetur eu. Vivamus dui lectus, mollis a condimentum consequat, ullamcorper porta lectus. Vivamus sit amet justo enim. Donec nec lorem mi. Lorem ipsum dolor sit amet, consectetur adipiscing elit. Nam condimentum leo sed nisi malesuada, sed accumsan metus ultricies. Donec eleifend nibh in ultrices tempus. Morbi id tempor lorem. Suspendisse potenti. Fusce at augue pulvinar, ultricies nisl id, bibendum est. Cras semper ac nulla ut vulputate. Nam faucibus sagittis odio, quis molestie elit sollicitudin et. Nam dapibus fringilla orci, quis efficitur leo consectetur eu. Vivamus dui lectus, mollis a condimentum consequat, ullamcorper porta lectus.</p>

  <div class="vote-options">
    <div class="vote vote-no">
      <div class="vote-ring"><svg width="24" height="24" viewBox="0 0 24 24"><path d="M3 3l18 18M21 3L3 21" stroke="var(--no-red)" stroke-width="3" stroke-linecap="round"/></svg></div>
      <span class="vote-label">No</span>
    </div>
    <div class="vote vote-party">
      <div class="vote-ring"><svg width="32" height="32" viewBox="0 0 32 32" fill="none" stroke="var(--navy)" stroke-width="2" stroke-linejoin="round"><path d="M6 8h20l-10 12z"/><path d="M9 12h14"/><path d="M16 20v7M11 28h10"/><circle cx="23" cy="6" r="3"/><path d="M14 4l4 8"/></svg></div>
      <span class="vote-label">Party</span>
    </div>
    <div class="vote vote-yes">
      <div class="vote-ring"><svg width="30" height="24" viewBox="0 0 30 24"><path d="M3 12l8 8L27 4" fill="none" stroke="var(--yes-green)" stroke-width="3" stroke-linecap="round" stroke-linejoin="round"/></svg></div>
      <span class="vote-label">Yes</span>
    </div>
  </div>

  <footer class="footer-bar">
    <span class="live-dot"></span>
    <div class="chamber">Legislative Council</div>
    <div class="position">1 / 77</div>
  </footer>
</body>
</html>
```